Business Card Design

We like to use greens as you will see in our logo (but not TOO much green). We are a Dental Clinic in a somewhat eccentric community. We do not like the dated sharp designs which we see many dentists use. We're looking for something bright and fresh while still maintaining the integrity of the profession. Elegance is not necessarily what we are going for... we need for the design to be "mature" but also up-lifting.

See our logo.
Updates

Project Deadline Extended
Reason: We have 5 designs which we like. But we'd like to see a few more before committing to a design.

Project Deadline Extended
Reason: We are awaiting revisions to this project. We are still welcoming designs while we wait to see if designers are able to provide to us the revisions we require in order to proceed with a selection.

Target Market(s)

Younger families - ages late 20's to early 40's

Industry/Entity Type

Business

Contact Information for Business Card

Corwel T. Banfry DDS 2730 W. Halvert Rd. Ste. 7 Maple Crest, WI 48391 (555)555-0174 FX (555)555-0189 info@BrightwellDentalCareMi.com BrigthwellDentalCareMi.com on the back of the card we need an appointment reminder (For____ Date___ Time____) with "If you are unable to keep your appointment, kindly give 48 hours notice" at the bottom. No use of teeth in the design. DOUBLE SIDED DESIGN

Requirements
Should not have
• The use of pictures of teeth

```html
<!DOCTYPE html>
<html lang="en">
<head>
<meta charset="utf-8">
<title>Brightwell Dental Care – Business Card</title>
<link rel="stylesheet" href="https://fonts.googleapis.com/css2?family=Open+Sans:ital,wght@0,400;0,700;1,400&family=Tinos:ital,wght@0,700;1,400&display=swap">
<style>
  :root {
    --backdrop: #e9ece6;
    --card: #ffffff;
    --lime: #92e61c;
    --forest: #2f7a12;
    --leaf: #5cb82a;
    --ink: #333333;
    --rule: #555555;
  }
  * { box-sizing: border-box; margin: 0; padding: 0; }
  html, body { width: 1200px; height: 492px; overflow: hidden; }
  body {
    background: var(--backdrop);
    font-family: "Open Sans", Arial, sans-serif;
    position: relative;
  }
  .card {
    position: absolute;
    top: 96px;
    width: 520px;
    height: 300px;
    background: var(--card);
    box-shadow: 0 4px 14px rgba(0,0,0,0.18);
    overflow: hidden;
  }
  .card--front { left: 50px; }
  .card--back { left: 630px; }

  .card__wave { position: absolute; inset: 0; width: 100%; height: 100%; }

  .brand {
    position: absolute;
    display: flex;
    align-items: center;
    gap: 10px;
    color: var(--forest);
    font-weight: 700;
    font-size: 25px;
    line-height: 1.05;
  }
  .brand__dot {
    width: 26px; height: 26px;
    border-radius: 50%;
    background: var(--lime);
    flex: none;
  }
  .card--front .brand { left: 36px; top: 42px; }
  .card--back .brand { left: 36px; top: 48px; }

  .doctor {
    position: absolute;
    right: 28px; top: 22px;
    font-weight: 700;
    font-size: 19px;
    color: var(--forest);
  }
  .doctor__title { color: var(--leaf); }

  .contact {
    position: absolute;
    right: 28px; top: 150px;
    list-style: none;
    text-align: right;
    color: #ffffff;
    font-size: 12.5px;
    line-height: 25px;
  }
  .contact__item { display: flex; justify-content: flex-end; align-items: center; gap: 5px; }
  .contact__icon { width: 11px; height: 11px; fill: #ffffff; }

  .address {
    position: absolute;
    left: 28px; bottom: 26px;
    color: #ffffff;
    font-size: 12.5px;
    line-height: 22px;
    font-style: normal;
  }

  .appointment {
    position: absolute;
    left: 36px; top: 150px; right: 30px;
    color: var(--ink);
  }
  .appointment__heading {
    font-family: "Tinos", "Times New Roman", serif;
    font-weight: 700;
    font-size: 16px;
    color: var(--forest);
    letter-spacing: 0.3px;
    border-bottom: 1px dotted var(--rule);
    padding-bottom: 4px;
    width: 340px;
  }
  .appointment__row {
    display: flex;
    align-items: flex-end;
    gap: 6px;
    font-size: 14px;
    margin-top: 16px;
  }
  .appointment__line { border-bottom: 1px solid var(--rule); height: 1px; margin-bottom: 4px; }
  .appointment__line--name { width: 290px; border-bottom-style: dotted; }
  .appointment__line--date { width: 95px; margin-right: 18px; }
  .appointment__line--time { width: 90px; }
  .appointment__note {
    font-family: "Tinos", "Times New Roman", serif;
    font-style: italic;
    font-size: 14.5px;
    color: #555555;
    margin-top: 18px;
  }
</style>
</head>
<body>

  <section class="card card--front" aria-label="Business card front">
    <svg class="card__wave" viewBox="0 0 520 300" preserveAspectRatio="none" aria-hidden="true">
      <path d="M0 206 C 190 188, 330 92, 520 64 L520 300 L0 300 Z" fill="var(--lime)"/>
      <path d="M0 172 C 170 160, 320 76, 520 52 L520 57 C 330 86, 190 180, 0 198 Z" fill="var(--forest)"/>
    </svg>

    <div class="brand">
      <span class="brand__dot"></span>
      <span class="brand__name">Brightwell<br>Dental Care</span>
    </div>

    <p class="doctor">Corwel T. Banfry<span class="doctor__title">, DDS</span></p>

    <ul class="contact">
      <li class="contact__item">
        <svg class="contact__icon" viewBox="0 0 12 12"><path d="M2.5 0.5 L4.5 0.5 L5.5 3.2 L4 4.3 C4.7 5.9 6 7.3 7.7 8 L8.8 6.5 L11.5 7.5 L11.5 9.5 C11.5 10.8 10.5 11.5 9.5 11.5 C4.5 11.2 0.8 7.5 0.5 2.5 C0.5 1.4 1.2 0.5 2.5 0.5 Z"/></svg>
        (555)555-0174
      </li>
      <li class="contact__item">
        <svg class="contact__icon" viewBox="0 0 12 12"><rect x="3" y="0.5" width="6" height="3.5"/><rect x="0.5" y="4.5" width="11" height="5" rx="1"/><rect x="3" y="8" width="6" height="3.5" fill="#ffffff" stroke="var(--lime)" stroke-width="0.8"/></svg>
        (555)555-0189
      </li>
      <li class="contact__item">
        <svg class="contact__icon" viewBox="0 0 12 12"><path d="M0.5 2 H11.5 V10 H0.5 Z M1 2.5 L6 6.5 L11 2.5" stroke="var(--lime)" stroke-width="0.8"/></svg>
        info@BrightwellDentalCareMi.com
      </li>
      <li class="contact__item">
        <svg class="contact__icon" viewBox="0 0 12 12"><circle cx="6" cy="6" r="5.5"/><path d="M0.5 6 H11.5 M6 0.5 C3.5 3.5 3.5 8.5 6 11.5 M6 0.5 C8.5 3.5 8.5 8.5 6 11.5" stroke="var(--lime)" stroke-width="0.8" fill="none"/></svg>
        www.BrigthwellDentalCareMi.com
      </li>
    </ul>

    <address class="address">
      2730 W. Halvert Rd. Ste.<br>
      7 Maple Crest, WI 48391
    </address>
  </section>

  <section class="card card--back" aria-label="Business card back">
    <div class="brand">
      <span class="brand__dot"></span>
      <span class="brand__name">Brightwell<br>Dental Care</span>
    </div>

    <div class="appointment">
      <h2 class="appointment__heading">YOUR APPOINTMENT</h2>
      <div class="appointment__row">
        <span>Name :</span><span class="appointment__line appointment__line--name"></span>
      </div>
      <div class="appointment__row">
        <span>Date :</span><span class="appointment__line appointment__line--date"></span>
        <span>Time :</span><span class="appointment__line appointment__line--time"></span><span>am / pm</span>
      </div>
      <p class="appointment__note">If you are unable to keep your appointment, kindly give 48 hours notice</p>
    </div>
  </section>

</body>
</html>
```